Business Card Design for a Personal Trainer

I need a business card design for my job as a personal trainer. It should have a unique, modern and exclusive design. On the front there should be only my logo with my name and my job. 0162/3819204 Tobias Lendhart Wiesengrundweg 14 80417 Munich Germany The most important contact information is the web adress. it can be bigger than the rest, but its not necessary. The card should be 8,5cmx5,5cm big. Font: Roboto. Colors: black, white, gray, 56c1ff.

```html
<!DOCTYPE html>
<html lang="de">
<head>
<meta charset="utf-8">
<title>Tobias Lendhart – Personal Trainer Business Card</title>
<link rel="stylesheet" href="https://fonts.googleapis.com/css2?family=Roboto:ital,wght@0,400;0,500;0,700;1,700;1,900&display=swap">
<style>
  :root {
    --page: #e9e7e4;
    --card-dark: #1d1d1d;
    --card-dark-soft: #262626;
    --card-light: #ffffff;
    --ink: #111111;
    --ink-soft: #555555;
    --gray: #9a9a9a;
    --photo-light: #ececec;
    --photo-mid: #9c9c9c;
  }
  * { box-sizing: border-box; margin: 0; padding: 0; }
  html, body { width: 1189px; height: 1200px; overflow: hidden; }
  body {
    background: var(--page);
    font-family: "Roboto", Arial, sans-serif;
    position: relative;
  }
  .card {
    position: absolute;
    left: 218px;
    width: 752px;
    height: 486px;
    border-radius: 20px;
    overflow: hidden;
  }
  .card--front {
    top: 76px;
    background: linear-gradient(135deg, var(--card-dark-soft), var(--card-dark) 60%);
    color: #ffffff;
  }
  .card--back {
    top: 605px;
    background: var(--card-light);
    color: var(--ink);
  }

  /* Front */
  .brand {
    position: absolute;
    left: 0; right: 0;
    top: 150px;
    text-align: center;
  }
  .brand__mark {
    display: block;
    width: 74px; height: 74px;
    margin: 0 auto 38px;
    border: 5px solid #ffffff;
    border-radius: 50%;
  }
  .brand__name {
    font-size: 39px;
    font-weight: 400;
    letter-spacing: 0.5px;
    line-height: 1;
  }
  .role {
    display: flex;
    align-items: center;
    justify-content: center;
    gap: 6px;
    margin-top: 7px;
    font-size: 15px;
    letter-spacing: 4px;
    line-height: 1;
  }
  .role::before, .role::after {
    content: "";
    width: 56px;
    height: 2px;
    background: currentColor;
  }
  .brand .role::before, .brand .role::after { width: 56px; }

  /* Back */
  .portrait {
    position: absolute;
    left: 82px; top: 132px;
    width: 248px; height: 248px;
    border-radius: 50%;
    border: 5px solid var(--ink);
    background: radial-gradient(circle at 50% 40%, var(--photo-light) 35%, var(--photo-mid) 100%);
  }
  .details {
    position: absolute;
    left: 383px;
    top: 162px;
    width: 300px;
  }
  .details__name {
    font-size: 31px;
    font-weight: 500;
    line-height: 1;
    letter-spacing: 0.2px;
  }
  .details .role {
    justify-content: flex-start;
    font-size: 12px;
    letter-spacing: 3px;
    margin-top: 4px;
  }
  .details .role::before { width: 44px; }
  .details .role::after { width: 44px; }
  .contact {
    list-style: none;
    margin-top: 64px;
  }
  .contact__item {
    display: flex;
    align-items: center;
    gap: 10px;
    font-size: 20px;
    line-height: 26px;
  }
  .contact__icon { width: 17px; height: 17px; fill: var(--gray); flex: none; }
  .website {
    margin-top: 16px;
    font-size: 19px;
    font-style: italic;
    font-weight: 900;
    letter-spacing: 2px;
  }
  .website__domain { color: var(--gray); font-weight: 700; }
</style>
</head>
<body>
  <section class="card card--front">
    <div class="brand">
      <span class="brand__mark"></span>
      <h1 class="brand__name">TOBIAS LENDHART</h1>
      <p class="role">PERSONAL TRAINER</p>
    </div>
  </section>

  <section class="card card--back">
    <div class="portrait" role="img" aria-label="Black and white portrait photo of the trainer"></div>
    <div class="details">
      <h2 class="details__name">TOBIAS LENDHART</h2>
      <p class="role">PERSONAL TRAINER</p>
      <ul class="contact">
        <li class="contact__item">
          <svg class="contact__icon" viewBox="0 0 24 24" aria-hidden="true"><path d="M6.6 10.8a15.1 15.1 0 0 0 6.6 6.6l2.2-2.2a1 1 0 0 1 1-.25 11.4 11.4 0 0 0 3.6.57 1 1 0 0 1 1 1V20a1 1 0 0 1-1 1A17 17 0 0 1 3 4a1 1 0 0 1 1-1h3.5a1 1 0 0 1 1 1c0 1.25.2 2.45.57 3.57a1 1 0 0 1-.25 1z"/></svg>
          <span>0162/3819204</span>
        </li>
        <li class="contact__item">
          <svg class="contact__icon" viewBox="0 0 24 24" aria-hidden="true"><path d="M2 5h20v14H2z M3.5 6.5 12 13l8.5-6.5" stroke="#fff" stroke-width="1.5"/></svg>
          <span>Info@yourgmail.com</span>
        </li>
      </ul>
      <p class="website">www.<span class="website__domain">YOURWEBSITE</span>.com</p>
    </div>
  </section>
</body>
</html>
```